Responsive OnePage Design for recruitment company

Norvessa Staffing is a modern company that sources interim people for its customers. Mostly developers, scrum master, project managers and designers. In this website we want to tell something about us, about how we work, our customers and we want our candidates be able to subscribe. The subscription form should be several fields (name, surname, email address, phone number and the possibility to upload your resume.We want it to fit into a existing wordpress plugin. We also want a listing of our job opportunities. The listing should be designed in a clear readable overview and if you click on the job you should get the details and be able to respond quickly by filling in you name, surname, email address, rate, phone number and upload your resume. We want this to be a standard configurable plugin. It should be easy to fill in the jobs in Wordpress by our administrator. We want a fresh, modern and cool design. It should be a responsive onepage design. If you click on a listed job you should stay on the same page. Our logo is added.

Target Market(s)

recruitment

Industry/Entity Type

Recruitment

Font styles to use
Sans Serif

Colors

Designer to choose colors to be used in the design.

Requirements
Must have
• Onepage design
• listing of job opportunities
• subscription forms
• be responsive

```html
<!DOCTYPE html>
<html lang="en">
<head>
<meta charset="utf-8">
<title>Norvessa Staffing – Interim Professionals</title>
<link href="https://fonts.googleapis.com/css2?family=Lato:wght@400;700;900&display=swap" rel="stylesheet">
<style>
:root{
  --blue:#1b5ea8;
  --blue-dark:#0f3f7a;
  --ink:#2b2b2b;
  --text:#555;
  --grey:#efefef;
  --line:#dcdcdc;
  --white:#fff;
  --num:#2f3133;
}
*{box-sizing:border-box;margin:0;padding:0}
html,body{width:1200px;height:3320px;overflow:hidden}
body{font-family:'Lato',Arial,sans-serif;color:var(--text);background:var(--white);position:relative}
.btn{display:inline-block;background:var(--blue);color:var(--white);font-weight:700;font-size:15px;letter-spacing:.5px;padding:11px 26px;border-radius:3px;text-transform:uppercase;white-space:nowrap}
.section-title{font-weight:900;font-size:40px;color:var(--ink);text-align:center;text-transform:uppercase;letter-spacing:.5px;white-space:nowrap}
.lead{font-size:14px;line-height:22px;text-align:center;color:var(--text)}

/* header */
.site-header{position:absolute;top:0;left:0;width:1200px;height:112px;background:var(--white);display:flex;align-items:center;justify-content:space-between;padding:0 80px;z-index:3}
.brand{font-size:28px;font-weight:700;letter-spacing:3px;color:var(--ink);text-transform:uppercase;white-space:nowrap}
.main-nav{display:flex;gap:28px}
.main-nav a{font-size:13px;font-weight:700;color:var(--ink);text-transform:uppercase;text-decoration:none;white-space:nowrap}

/* hero */
.hero{position:absolute;top:112px;left:0;width:1200px;height:468px;overflow:hidden}
.hero-visual{position:absolute;inset:0;background:linear-gradient(100deg,#8fb0cc 0%,#c7d9e8 40%,#e3ebf2 60%,#b7c9d9 100%)}
.hero-copy{position:absolute;left:70px;top:120px;width:640px;color:var(--white)}
.hero-copy h1{font-size:50px;font-weight:900;letter-spacing:1px;text-transform:uppercase;white-space:nowrap}
.hero-copy p{font-size:14px;line-height:22px;margin:14px 0 24px;width:480px}
.hero-dots{position:absolute;left:70px;top:385px;display:flex;gap:8px}
.hero-dots span{width:10px;height:10px;border-radius:50%;background:rgba(255,255,255,.6)}
.hero-dots span:first-child{background:var(--white)}
.hero-curve{position:absolute;left:0;bottom:0}

/* about */
.about{position:absolute;top:580px;left:80px;width:1040px;height:340px;background:var(--grey);display:flex;padding:20px}
.about-photo{width:490px;height:300px;flex:none;background:linear-gradient(135deg,#c9cfd6,#8c98a6 60%,#5c6877)}
.about-copy{padding:30px 30px 0 36px;flex:1}
.about-copy h2{font-size:34px;font-weight:900;color:var(--ink);text-transform:uppercase;white-space:nowrap}
.about-copy h2 span{color:var(--blue)}
.about-copy p{font-size:14px;line-height:21px;margin-top:14px}
.about-copy .btn{margin-top:20px}

/* how we work */
.how{position:absolute;top:1050px;left:0;width:1200px}
.how .lead{width:820px;margin:14px auto 0}
.how-video{position:relative;width:864px;height:380px;margin:30px auto 0;background:linear-gradient(135deg,#2f8a80,#3aa196 50%,#287568)}
.play{position:absolute;left:50%;top:50%;transform:translate(-50%,-50%)}

/* jobs */
.jobs{position:absolute;top:1610px;left:0;width:1200px;height:730px;background:var(--grey)}
.jobs .section-title{position:absolute;top:44px;width:100%}
.job-list{list-style:none;position:absolute;top:116px;left:72px;width:1056px}
.job{display:flex;align-items:center;height:84px;background:var(--white);margin-bottom:28px;box-shadow:0 2px 4px rgba(0,0,0,.08)}
.job-num{width:80px;height:84px;flex:none;background:var(--num);color:var(--white);font-size:30px;font-weight:900;display:flex;align-items:center;justify-content:center}
.job-field{font-size:12px;line-height:18px;color:var(--ink);text-transform:uppercase;white-space:nowrap}
.job-field b{display:block;color:var(--blue);font-weight:700}
.job-pos{width:350px;margin-left:40px}
.job-loc{width:300px}
.job-exp{width:140px}
.job .btn{font-size:13px;padding:10px 40px;margin-left:14px}

/* services */
.services{position:absolute;top:2400px;left:0;width:1200px}
.service-grid{display:flex;gap:20px;padding:0 72px;margin-top:36px}
.service{flex:1;height:280px;border:1px solid var(--line);box-shadow:0 2px 5px rgba(0,0,0,.06);text-align:center;padding-top:36px}
.service h3{font-size:16px;font-weight:900;color:var(--blue);text-transform:uppercase;margin-top:22px;white-space:nowrap}
.service p{font-size:13px;line-height:19px;margin:10px 26px 0}

/* subscription */
.subscribe{position:absolute;top:2790px;left:0;width:1200px;height:370px;background:linear-gradient(180deg,#1c65b3,#0e4485)}
.subscribe-curve{position:absolute;top:0;left:0}
.subscribe h2{position:absolute;top:88px;width:100%;text-align:center;color:var(--white);font-size:40px;font-weight:900;text-transform:uppercase}
.sub-form{position:absolute;top:166px;left:250px;width:700px;display:grid;grid-template-columns:1fr 1fr;gap:14px 24px}
.sub-form .field{height:44px;background:var(--white);font-size:12px;font-weight:700;color:var(--ink);padding:14px;text-transform:uppercase}
.uploads{display:flex;gap:16px}
.upload{height:44px;padding:0 22px;font-size:14px;display:flex;align-items:center;border:1px solid var(--white);color:var(--white);white-space:nowrap}
.upload.solid{background:var(--white);color:var(--ink);font-weight:700}
.submit{height:44px;background:#111;color:var(--white);font-weight:700;font-size:14px;display:flex;align-items:center;justify-content:center;text-transform:uppercase}

/* footer */
.site-footer{position:absolute;top:3160px;left:0;width:1200px;height:160px;text-align:center;padding-top:48px;font-size:13px;color:var(--ink)}
.social{display:flex;gap:18px;justify-content:center;margin-top:20px}
.social span{width:18px;height:18px;border-radius:50%;background:var(--ink)}
</style>
</head>
<body>

<header class="site-header">
  <div class="brand">Norvessa Staffing</div>
  <nav class="main-nav">
    <a>About Us</a><a>How We Work</a><a>Job Opportunities</a><a>Services</a><a>Subscription</a><a>Contact Us</a>
  </nav>
</header>

<section class="hero">
  <div class="hero-visual" role="img" aria-label="Hand holding a transparent tablet showing a network of candidate profile icons"></div>
  <div class="hero-copy">
    <h1>Norvessa Staffing</h1>
    <p>Lorem ipsum dolor sit amet, consectetur adipiscing elit ut ultricies lectus. Donec porttitor, nisl ac pellentesque faucibus, ante ante imperdiet augue, ut sodales sapien metus et mauris.</p>
    <span class="btn">Read More</span>
  </div>
  <div class="hero-dots"><span></span><span></span><span></span><span></span></div>
  <svg class="hero-curve" width="1200" height="120" viewBox="0 0 1200 120" aria-hidden="true">
    <path d="M0 120 L0 95 Q600 20 1200 70 L1200 120 Z" fill="#fff"/>
  </svg>
</section>

<section class="about">
  <div class="about-photo" role="img" aria-label="Business people shaking hands in a bright office"></div>
  <div class="about-copy">
    <h2>About Norvessa <span>Staffing</span></h2>
    <p>Lorem ipsum dolor sit amet, consectetur adipiscing elit ut ultricies lectus. Donec porttitor, nisl ac pellentesque faucibus, ante ante imperdiet augue, ut sodales sapien metus et mauris.</p>
    <p>Donec finibus convallis viverra. Fusce orci turpis, ultrices quis metus vitae, vulputate facilisis metus. Proin porttitor quam nec elit viverra tincidunt vel vitae massa. Maecenas aliquet pharetra lorem. Donec a augue suscipit, lacinia diam non, convallis nisl.</p>
    <span class="btn">Read More</span>
  </div>
</section>

<section class="how">
  <h2 class="section-title">How We Work</h2>
  <p class="lead">Lorem ipsum dolor sit amet, consectetur adipiscing elit. Praesent at ultricies lectus. Donec porttitor, nisl ac pellentesque faucibus, ante ante imperdiet augue, ut sodales sapien metus et mauris.</p>
  <div class="how-video" role="img" aria-label="Video cover: isometric office scene with professionals at work">
    <svg class="play" width="72" height="72" viewBox="0 0 72 72" aria-hidden="true">
      <circle cx="36" cy="36" r="34" fill="#fff"/>
      <path d="M29 22 L52 36 L29 50 Z" fill="#222"/>
    </svg>
  </div>
</section>

<section class="jobs">
  <h2 class="section-title">Featured Job Opportunities</h2>
  <ul class="job-list">
    <li class="job"><div class="job-num">1.</div><div class="job-field job-pos"><b>Position:</b>Crastinbus lacinia elit sit amet dictum</div><div class="job-field job-loc"><b>Location:</b>Elit sit amet dictum</div><div class="job-field job-exp"><b>Experience:</b>5yrs +</div><span class="btn">Apply Now</span></li>
    <li class="job"><div class="job-num">2.</div><div class="job-field job-pos"><b>Position:</b>Crastinbus lacinia elit sit amet dictum</div><div class="job-field job-loc"><b>Location:</b>Elit sit amet dictum</div><div class="job-field job-exp"><b>Experience:</b>5yrs +</div><span class="btn">Apply Now</span></li>
    <li class="job"><div class="job-num">3.</div><div class="job-field job-pos"><b>Position:</b>Crastinbus lacinia elit sit amet dictum</div><div class="job-field job-loc"><b>Location:</b>Elit sit amet dictum</div><div class="job-field job-exp"><b>Experience:</b>5yrs +</div><span class="btn">Apply Now</span></li>
    <li class="job"><div class="job-num">4.</div><div class="job-field job-pos"><b>Position:</b>Crastinbus lacinia elit sit amet dictum</div><div class="job-field job-loc"><b>Location:</b>Elit sit amet dictum</div><div class="job-field job-exp"><b>Experience:</b>5yrs +</div><span class="btn">Apply Now</span></li>
    <li class="job"><div class="job-num">5.</div><div class="job-field job-pos"><b>Position:</b>Crastinbus lacinia elit sit amet dictum</div><div class="job-field job-loc"><b>Location:</b>Elit sit amet dictum</div><div class="job-field job-exp"><b>Experience:</b>5yrs +</div><span class="btn">Apply Now</span></li>
  </ul>
</section>

<section class="services">
  <h2 class="section-title">Services Offer For</h2>
  <div class="service-grid">
    <div class="service">
      <svg width="60" height="48" viewBox="0 0 60 48" aria-hidden="true"><rect x="8" y="4" width="44" height="30" rx="2" fill="none" stroke="#2b2b2b" stroke-width="3"/><path d="M22 44 H38 M30 34 V44" stroke="#2b2b2b" stroke-width="3"/></svg>
      <h3>Developers</h3>
      <p>Lorem ipsum dolor sit amet, consectetur adipiscing elit. Praesent ut ultricies lectus porttitor quam.</p>
    </div>
    <div class="service">
      <svg width="60" height="48" viewBox="0 0 60 48" aria-hidden="true"><circle cx="30" cy="14" r="9" fill="#2b2b2b"/><path d="M12 46 Q30 18 48 46 Z" fill="#2b2b2b"/></svg>
      <h3>Scrum Master</h3>
      <p>Lorem ipsum dolor sit amet, consectetur adipiscing elit. Praesent ut ultricies lectus porttitor quam.</p>
    </div>
    <div class="service">
      <svg width="60" height="48" viewBox="0 0 60 48" aria-hidden="true"><rect x="6" y="4" width="48" height="32" fill="none" stroke="#2b2b2b" stroke-width="3"/><path d="M14 28 L24 18 L32 24 L46 12" fill="none" stroke="#2b2b2b" stroke-width="3"/><path d="M20 46 L30 36 L40 46" fill="none" stroke="#2b2b2b" stroke-width="3"/></svg>
      <h3>Project Managers</h3>
      <p>Lorem ipsum dolor sit amet, consectetur adipiscing elit. Praesent ut ultricies lectus porttitor quam.</p>
    </div>
    <div class="service">
      <svg width="60" height="48" viewBox="0 0 60 48" aria-hidden="true"><path d="M14 42 L18 30 L42 6 L50 14 L26 38 Z" fill="none" stroke="#2b2b2b" stroke-width="3"/><path d="M10 46 H50" stroke="#2b2b2b" stroke-width="3"/></svg>
      <h3>Designers</h3>
      <p>Lorem ipsum dolor sit amet, consectetur adipiscing elit. Praesent ut ultricies lectus porttitor quam.</p>
    </div>
  </div>
</section>

<section class="subscribe">
  <svg class="subscribe-curve" width="1200" height="80" viewBox="0 0 1200 80" aria-hidden="true">
    <path d="M0 0 H1200 V10 Q600 80 0 30 Z" fill="#fff"/>
  </svg>
  <h2>Subscription Forms</h2>
  <div class="sub-form">
    <div class="field">Name</div>
    <div class="field">Surname</div>
    <div class="field">Email</div>
    <div class="field">Phone</div>
    <div class="uploads"><span class="upload">Upload File</span><span class="upload solid">Upload Resume</span></div>
    <div class="submit">Subscribe Now</div>
  </div>
</section>

<footer class="site-footer">
  <p>Copyright © 2019 Company Name. All Rights Reserved.</p>
  <div class="social"><span></span><span></span><span></span><span></span><span></span></div>
</footer>

</body>
</html>
```